Brimsett Gardening Fresh New Website

We are looking to create a simple fresh website for our landscaping business. The website should appeal to a 'high end' audience. We deal with a lot of Embassies and affluent clients who have extremely large gardens that are meticulously maintained. The site is about communicating our excellent landscaping and customer service skills and encouraging new clients to reach out and engage us to take care of their gardens.

The website is basically going to be our business card, it will have almost no functionality other than two 'contact us' forms, one for smaller clients and one for more detailed projects.

The website will not have a lot of written content and will have to show photos of beautifully landscaped gardens.

The main logo in black will influence the site, however, we are open to all suggestions.

We are expecting to have the following pages:
Home Page
Services
About Us
Contact Us
Showcase (photo gallery of our work)

We need someone who can code it to wordpress and be available for minor changes over a number of days. They will be simple tweaks.

```html
<!DOCTYPE html>
<html lang="en">
<head>
<meta charset="utf-8">
<title>Brimsett Gardening</title>
<link href="https://fonts.googleapis.com/css2?family=Gelasio:wght@500;600;700&family=Poppins:wght@400;500;600&display=swap" rel="stylesheet">
<style>
:root{
  --gold-dark:#b08524;
  --gold-light:#f5d544;
  --gold-text:#b58a2a;
  --ink:#111111;
  --body:#333333;
  --muted:#f4f4f4;
  --white:#ffffff;
  --footer:#161616;
  --gold-grad:linear-gradient(90deg,var(--gold-dark),var(--gold-light));
}
*{margin:0;padding:0;box-sizing:border-box}
html,body{width:1200px;height:4132px;overflow:hidden}
body{position:relative;background:var(--white);font-family:"Poppins",sans-serif;color:var(--body)}
.section{position:absolute;left:0;width:1200px}
.abs{position:absolute}
.heading{position:absolute;left:0;width:1200px;text-align:center;font-family:"Gelasio",serif;font-weight:700;font-size:38px;color:var(--ink)}
.heading span{color:var(--gold-text)}
.btn{position:absolute;display:flex;align-items:center;justify-content:center;background:var(--gold-grad);color:#2a1d00;font-size:12px;font-weight:600}
.photo{position:absolute}

/* hero */
.hero{top:0;height:589px}
.hero-bg{position:absolute;inset:0;background:linear-gradient(180deg,#2e3a2c 0%,#4a5646 35%,#3f5a2e 65%,#2c4420 100%)}
.brand{position:absolute;color:var(--white);font-family:"Gelasio",serif;font-weight:500;letter-spacing:4px;text-transform:uppercase;text-align:center;line-height:1.4}
.brand-dot{width:26px;height:26px;border:1.5px solid currentColor;border-radius:50%;margin:0 auto 6px}
.nav a{position:absolute;top:82px;color:var(--white);font-size:12.5px;text-decoration:none;transform:translateX(-50%)}
.quote-top{position:absolute;left:906px;top:21px;width:151px;height:34px;background:#0c0c0c;color:var(--white);font-size:12px;font-weight:500;display:flex;align-items:center;justify-content:center;gap:8px}
.follow{position:absolute;left:55px;top:176px;color:var(--white);font-size:12px;letter-spacing:1.5px;writing-mode:vertical-rl}
.social-dot{position:absolute;left:55px;width:16px;height:16px;border:1.6px solid var(--white);border-radius:50%}
.hero-kicker{position:absolute;left:141px;top:226px;color:var(--white);font-size:22px;letter-spacing:3px;font-weight:500}
.hero-title{position:absolute;left:141px;top:266px;color:var(--white);font-family:"Gelasio",serif;font-weight:600;font-size:42px;line-height:56px}
.quote-panel{position:absolute;left:701px;top:135px;width:358px;height:433px;background:rgba(215,215,210,.78)}
.quote-panel h2{position:absolute;left:17px;top:18px;font-family:"Gelasio",serif;font-weight:600;font-size:21px;line-height:27px;color:#1a1a1a}
.panel-mark{position:absolute;right:22px;top:12px;width:42px;height:42px;border:1.5px solid var(--gold-text);border-radius:50%;opacity:.6}
.field{position:absolute;background:rgba(255,255,255,.55);border:1px solid rgba(255,255,255,.75);font-size:11.5px;color:#333;padding:0 13px;display:flex;align-items:center}
.field b{color:#d03030;font-weight:400}
.panel-field{left:21px;width:314px;height:33px}

/* services */
.services{top:589px;height:595px}
.card{position:absolute;top:125px;width:291px;height:313px;background:var(--white);box-shadow:0 8px 22px rgba(0,0,0,.12)}
.card .photo{left:0;top:0;width:291px;height:172px}
.card-icon{position:absolute;left:108px;top:133px;width:76px;height:76px;border-radius:50%;background:var(--white);display:flex;align-items:center;justify-content:center}
.card h3{position:absolute;top:200px;width:100%;text-align:center;font-family:"Gelasio",serif;font-weight:600;font-size:17px;color:var(--ink)}
.card p{position:absolute;top:234px;left:12px;right:12px;text-align:center;font-size:11px;line-height:22.5px;color:#333}

/* about */
.about{top:1184px;height:508px;background:var(--muted)}
.about h2{position:absolute;left:141px;top:92px;font-family:"Gelasio",serif;font-weight:700;font-size:37px;line-height:45px;color:var(--ink)}
.about h2 span{color:var(--gold-text)}
.about p{position:absolute;left:141px;width:470px;font-size:11px;line-height:22.5px;color:#333}
.frame{position:absolute;left:661px;top:86px;width:397px;height:323px;border:2px solid var(--gold-text)}

/* reviews */
.reviews{top:1692px;height:465px}
.review-back{position:absolute;left:310px;top:200px;width:580px;height:182px;background:var(--white);box-shadow:0 8px 20px rgba(0,0,0,.08)}
.review-card{position:absolute;left:282px;top:181px;width:634px;height:183px;background:var(--white);box-shadow:0 4px 20px rgba(0,0,0,.1)}
.review-card p{position:absolute;left:40px;right:40px;top:40px;text-align:center;font-size:11px;line-height:22.5px;color:#222}
.review-name{position:absolute;left:0;right:0;top:119px;text-align:center;font-size:13px;font-weight:500;color:#111}
.quote-badge{position:absolute;left:563px;top:151px;width:58px;height:58px;border-radius:50%;background:var(--gold-grad);display:flex;align-items:center;justify-content:center}

/* banner */
.banner{top:2157px;height:430px}
.banner-bg{position:absolute;inset:0;background:linear-gradient(180deg,#3a3a34 0%,#4d4a40 40%,#3c3a33 75%,#2e2c27 100%)}
.banner h2{position:absolute;left:0;width:1200px;top:134px;text-align:center;font-family:"Gelasio",serif;font-weight:700;font-size:38px;color:var(--white)}
.banner p{position:absolute;left:190px;width:820px;top:194px;text-align:center;font-size:11.3px;line-height:22.5px;color:var(--white)}

/* gallery */
.gallery{top:2587px;height:753px}
.tile{position:absolute;width:292px;height:217px}
.tile-overlay{background:rgba(40,40,35,.9);color:var(--white);text-align:center}
.tile-overlay h3{position:absolute;top:44px;width:100%;font-family:"Gelasio",serif;font-weight:600;font-size:17px}
.tile-overlay p{position:absolute;top:82px;left:16px;right:16px;font-size:11px;line-height:22.5px}

/* inquiry */
.inquiry{top:3340px;height:465px;background:var(--muted)}
.inq-field{background:var(--white);border:1px solid #ececec;height:31px}

/* footer */
.footer{top:3805px;height:292px;background:var(--footer);color:var(--white)}
.footer h4{position:absolute;top:70px;font-size:13.5px;font-weight:500}
.footer a,.footer span.item{position:absolute;font-size:12px;color:var(--white);text-decoration:none}
.f-icon{position:absolute;width:36px;height:36px;border-radius:50%;background:var(--gold-grad);display:flex;align-items:center;justify-content:center}
.bottom-bar{top:4097px;height:35px;background:var(--gold-grad);display:flex;align-items:center;justify-content:center;font-size:12px;color:#1a1200}
</style>
</head>
<body>

<header class="section hero">
  <div class="hero-bg" role="img" aria-label="Photo of a large white country house behind a wide green lawn and tall trees"></div>
  <div class="brand" style="left:134px;top:24px;width:120px;font-size:15px">
    <div class="brand-dot"></div>Brimsett<br><span style="font-size:9px;letter-spacing:4px">Gardening</span>
  </div>
  <div class="quote-top">Request A Quote
    <svg width="12" height="8" viewBox="0 0 12 8"><path d="M1 1l5 5 5-5" fill="none" stroke="#fff" stroke-width="1.6"/></svg>
  </div>
  <nav class="nav">
    <a style="left:553px">Home</a>
    <a style="left:666px">Services</a>
    <a style="left:781px">Gallery</a>
    <a style="left:898px">About Us</a>
    <a style="left:1027px">Contact Us</a>
  </nav>
  <div class="follow">Follow Us</div>
  <div class="social-dot" style="top:263px"></div>
  <div class="social-dot" style="top:301px"></div>
  <div class="social-dot" style="top:340px"></div>
  <div class="hero-kicker">LANDSCAPE PROS</div>
  <h1 class="hero-title">Stunning Landscapes<br>To Inspire Your Family</h1>
  <div class="btn" style="left:141px;top:390px;width:132px;height:34px">Request A Quote</div>

  <form class="quote-panel">
    <h2>24% Off For New<br>Landscape Services</h2>
    <div class="panel-mark"></div>
    <div class="field panel-field" style="top:85px">Name<b>*</b></div>
    <div class="field panel-field" style="top:128px">Email<b>*</b></div>
    <div class="field panel-field" style="top:170px">Phone Number<b>*</b></div>
    <div class="field panel-field" style="top:213px">Street Address &amp; Zip Code<b>*</b></div>
    <div class="field panel-field" style="top:255px;justify-content:space-between">Which Service Would You Like A Bill For?
      <svg width="12" height="8" viewBox="0 0 12 8"><path d="M1 1l5 5 5-5" fill="none" stroke="#222" stroke-width="1.6"/></svg>
    </div>
    <div class="field panel-field" style="top:297px;height:68px;align-items:flex-start;padding-top:10px">Message</div>
    <div class="btn" style="left:21px;top:374px;width:314px;height:35px">Request A Quote</div>
  </form>
</header>

<section class="section services">
  <h2 class="heading" style="top:50px">Our <span>Services</span></h2>
  <article class="card" style="left:141px">
    <div class="photo" role="img" aria-label="Photo of a lush lawn bordered by flowering shrubs" style="background:linear-gradient(180deg,#4f7d38,#c94f6a 45%,#4aa52a 70%,#3b8f22)"></div>
    <div class="card-icon"><svg width="40" height="32" viewBox="0 0 40 32"><path d="M4 22h32M8 22l-2-14M14 22l-1-16M20 22V4M26 22l1-16M32 22l2-14" stroke="#b58a2a" stroke-width="1.8" fill="none"/><rect x="6" y="24" width="28" height="5" fill="none" stroke="#222" stroke-width="1.4"/></svg></div>
    <h3>Lawn Fertilizing</h3>
    <p>Lorem Ipsum Is Simply Dummy Text Of The Printing And Typesetting Industry. Contrary Belief, Lorem Ipsum Random Text.</p>
  </article>
  <article class="card" style="left:454px">
    <div class="photo" role="img" aria-label="Photo of a patio with outdoor sofas behind a white fence" style="background:linear-gradient(180deg,#6f8a5e,#d9d6cc 45%,#8a7d6a 80%,#5e5448)"></div>
    <div class="card-icon"><svg width="36" height="36" viewBox="0 0 36 36"><path d="M6 14L18 5l12 9" stroke="#b58a2a" stroke-width="2" fill="none"/><path d="M8 16h20M12 16v14M24 16v14M6 24h8M22 24h8M18 16v8" stroke="#222" stroke-width="2" fill="none"/></svg></div>
    <h3>Patios</h3>
    <p>Lorem Ipsum Is Simply Dummy Text Of The Printing And Typesetting Industry. Contrary Belief, Lorem Ipsum Random Text.</p>
  </article>
  <article class="card" style="left:767px">
    <div class="photo" role="img" aria-label="Photo of a gardener spraying leafy plants" style="background:linear-gradient(90deg,#3e6d2e,#6d9a4a 55%,#2b3e7a)"></div>
    <div class="card-icon"><svg width="36" height="36" viewBox="0 0 36 36"><path d="M18 4v24M18 28l-10-8M18 28l10-8M18 22L8 10M18 22l10-12" stroke="#222" stroke-width="1.6" fill="none"/><circle cx="24" cy="28" r="4" fill="none" stroke="#b58a2a" stroke-width="1.6"/></svg></div>
    <h3>Weed Control</h3>
    <p>Lorem Ipsum Is Simply Dummy Text Of The Printing And Typesetting Industry. Contrary Belief, Lorem Ipsum Random Text.</p>
  </article>
  <div class="btn" style="left:534px;top:476px;width:132px;height:34px">Request A Quote</div>
</section>

<section class="section about">
  <h2>About<br><span>Brimsett Gardening</span></h2>
  <p style="top:194px">Lorem Ipsum Is Simply Dummy Text Of The Printing And Typesetting Industry. Lorem Ipsum Has Been The Industry's Standard Dummy Text Ever Since The 1500s, When An Unknown Printer Took A Galley Of Type And Scrambled It To Make A Type Specimen Book.</p>
  <p style="top:290px">Lorem Ipsum Is Simply Dummy Text Of The Printing And Typesetting Industry. Lorem Ipsum Has Been The Industry's Standard Dummy Text Ever Since The 1500s, When And Scrambled It To Make A Type Specimen Book.</p>
  <div class="btn" style="left:141px;top:378px;width:93px;height:32px">Read More</div>
  <div class="frame"></div>
  <div class="photo" role="img" aria-label="Photo of a large grey-shingled house with a white porch and green lawn" style="left:645px;top:99px;width:399px;height:324px;background:linear-gradient(180deg,#cfe1ef 0%,#e9eef2 35%,#7c8a95 55%,#5c8f34 80%,#4a8228 100%)"></div>
</section>

<section class="section reviews">
  <h2 class="heading" style="top:70px">Customer <span>Reviews</span></h2>
  <div class="review-back"></div>
  <div class="review-card">
    <p>Lorem Ipsum Is Simply Dummy Text Of The Printing And Typesetting Industry. Lorem Ipsum Has Been The Industry's Standard Dummy Text Ever Since The 1500s, When An Unknown Printer Took A Galley Of Type And Scrambled It To Make A Type Specimen Book.</p>
    <div class="review-name">– Edmund. R</div>
    <svg class="abs" style="left:295px;top:148px" width="44" height="12" viewBox="0 0 44 12"><path d="M18 6H2M7 1L2 6l5 5" stroke="#222" stroke-width="1.5" fill="none"/><path d="M26 6h16M37 1l5 5-5 5" stroke="#b58a2a" stroke-width="1.5" fill="none"/></svg>
  </div>
  <div class="quote-badge"><svg width="30" height="22" viewBox="0 0 30 22"><path d="M12 2C5 4 2 9 2 14a6 6 0 1 0 6-6c1-2 3-4 5-4zM28 2c-7 2-10 7-10 12a6 6 0 1 0 6-6c1-2 3-4 5-4z" fill="#1a1200"/></svg></div>
</section>

<section class="section banner">
  <div class="banner-bg" role="img" aria-label="Photo of a covered patio with wooden benches, cushioned seating and potted plants"></div>
  <h2>Build Your Outdoor Dream With Us</h2>
  <p>Lorem Ipsum Is Simply Dummy Text Of The Printing And Typesetting Industry. Lorem Ipsum Has Been The Industry's Standard Dummy Text Ever Since The 1500s, When An Unknown Printer Took A Galley Of Type And Scrambled It To Make A Type Specimen Book.</p>
  <div class="btn" style="left:550px;top:255px;width:98px;height:34px">Contact Us</div>
</section>

<section class="section gallery">
  <h2 class="heading" style="top:72px">Work <span>Gallery</span></h2>
  <div class="tile" role="img" aria-label="Photo of a golf green surrounded by pine trees" style="left:141px;top:151px;background:linear-gradient(180deg,#aab6a6,#35502c 45%,#6ea43a 80%,#4f8a28)"></div>
  <div class="tile" role="img" aria-label="Close-up photo of grass blades" style="left:454px;top:151px;background:linear-gradient(135deg,#3f7a2a,#8fc05a 50%,#356b22)"></div>
  <div class="tile" role="img" aria-label="Photo of a round hay bale on a grassy field" style="left:767px;top:151px;background:linear-gradient(180deg,#8fa34a,#7a8060 50%,#6f8a32)"></div>
  <div class="tile" role="img" aria-label="Photo of a worker rolling out fresh turf" style="left:141px;top:390px;background:linear-gradient(135deg,#2f4a8a 0%,#6f9a44 40%,#7a6550 75%,#5c4a3a)"></div>
  <div class="tile tile-overlay" style="left:454px;top:390px">
    <h3>Lorem Ipsum Text</h3>
    <p>Lorem Ipsum Has Been The Industry's Standard Dummy Text Ever Since The 1500s, When An Galley Of Type And Scrambled It To Make A Type Specimen Book.</p>
  </div>
  <div class="tile" role="img" aria-label="Photo of a brick path curving through a green park" style="left:767px;top:390px;background:linear-gradient(180deg,#cfe0f0,#4f9a2e 35%,#6fb83a 65%,#a0604a 90%)"></div>
  <div class="btn" style="left:551px;top:634px;width:98px;height:33px">Contact Us</div>
</section>

<section class="section inquiry">
  <h2 class="heading" style="top:74px">Quick <span>Inquiry</span></h2>
  <div class="field inq-field" style="left:289px;top:160px;width:304px">First Name*</div>
  <div class="field inq-field" style="left:606px;top:160px;width:304px">Last Name*</div>
  <div class="field inq-field" style="left:289px;top:205px;width:304px">Email*</div>
  <div class="field inq-field" style="left:606px;top:205px;width:304px">Phone Number*</div>
  <div class="field inq-field" style="left:289px;top:251px;width:621px;height:82px;align-items:flex-start;padding-top:10px">Message</div>
  <div class="btn" style="left:289px;top:349px;width:621px;height:31px">Submit</div>
</section>

<footer class="section footer">
  <div class="brand" style="left:141px;top:68px;width:148px;color:var(--gold-text);font-size:22px;letter-spacing:6px">
    <div class="brand-dot" style="width:34px;height:34px"></div>Brimsett<br><span style="font-size:11px;letter-spacing:6px">Gardening</span>
  </div>

  <h4 style="left:414px">Quick Links</h4>
  <a style="left:414px;top:96px">Home</a>
  <a style="left:414px;top:122px">Services</a>
  <a style="left:414px;top:147px">Gallery</a>
  <a style="left:414px;top:173px">About Us</a>
  <a style="left:414px;top:198px">FAQs</a>
  <a style="left:414px;top:223px">Contact Us</a>

  <h4 style="left:616px">Contact Details</h4>
  <div class="f-icon" style="left:616px;top:94px"><svg width="14" height="18" viewBox="0 0 14 18"><path d="M7 17s6-6 6-10A6 6 0 0 0 1 7c0 4 6 10 6 10z" fill="none" stroke="#1a1200" stroke-width="1.5"/><circle cx="7" cy="7" r="2" fill="none" stroke="#1a1200" stroke-width="1.5"/></svg></div>
  <span class="item" style="left:666px;top:97px;line-height:15px">123, Street Name, City<br>Name, Country Name,&nbsp; 1234</span>
  <div class="f-icon" style="left:616px;top:142px"><svg width="16" height="16" viewBox="0 0 16 16"><path d="M3 1l3 3-2 2c1 2 3 4 6 6l2-2 3 3-2 2C7 15 1 9 1 3z" fill="none" stroke="#1a1200" stroke-width="1.4"/></svg></div>
  <span class="item" style="left:666px;top:152px">123 456 7890</span>
  <div class="f-icon" style="left:616px;top:192px"><svg width="16" height="12" viewBox="0 0 16 12"><rect x="1" y="1" width="14" height="10" fill="none" stroke="#1a1200" stroke-width="1.4"/><path d="M1 1l7 6 7-6" fill="none" stroke="#1a1200" stroke-width="1.4"/></svg></div>
  <span class="item" style="left:666px;top:201px">Brimsettgardening@Postleaf.Com</span>

  <h4 style="left:951px">Follow Us</h4>
  <div class="f-icon" style="left:951px;top:94px"></div>
  <span class="item" style="left:1000px;top:103px">Leafbook</span>
  <div class="f-icon" style="left:951px;top:142px"></div>
  <span class="item" style="left:1000px;top:152px">Snapgrove</span>
  <div class="f-icon" style="left:951px;top:192px"></div>
  <span class="item" style="left:1000px;top:201px">Workline</span>
</footer>
<div class="section bottom-bar">© 2024 Brimsett Gardening. All Rights Reserved.</div>

</body>
</html>
```